Dental Medical History Form - Content provided

Design a medical history form for a dental practice. Content is provided so all that is needed is the formatting to make it look great and easy to read.

"Patient Information" to include all information contained in top portion of the "Patient Medical History Form" docx file.

"Medical History" should follow the formatting and content of the "Exact Medical History" file as this is what the entry fields look like in our practice software and so we would like it to match.

1st page - Patient info, allergies, medications, antibiotics, joint replacement, pregnancy.

2nd page - Do you have, or have you had, any of the following? . . . . . . .
Updates

Target Market(s)

All ages but must be clear enough for elderly to read. Use as much space as possible to keep font size bigger yet keep to two pages

Industry/Entity Type

Dental

Font styles to use
Sans Serif

Requirements
Must have
• All content provided
• Our logo at the top (file provided)
• Century Gothic Font
• Limit to two pages

```html
<!DOCTYPE html>
<html lang="en">
<head>
<meta charset="utf-8">
<title>Harbour Dental – Confidential Medical History</title>
<link href="https://fonts.googleapis.com/css2?family=Didact+Gothic&display=swap" rel="stylesheet">
<style>
  :root{
    --backdrop:#5b3e2c;
    --page:#ffffff;
    --ink:#1b1b1b;
    --muted:#444444;
    --field:#e6e6e6;
    --bar:#111111;
    --frame:#c4c4c4;
    --box:#7a7a7a;
  }
  *{box-sizing:border-box;margin:0;padding:0}
  html,body{width:1200px;height:1000px;overflow:hidden}
  body{background:var(--backdrop);font-family:"Didact Gothic",sans-serif;color:var(--ink);position:relative}

  .page{position:absolute;top:102px;width:563px;height:796px;background:var(--page);box-shadow:0 2px 8px rgba(0,0,0,.35)}
  .page--front{left:27px}
  .page--back{left:612px}
  .page__frame{position:absolute;left:13px;top:16px;right:13px;bottom:16px;border:1px solid var(--frame);border-radius:32px}

  .abs{position:absolute;white-space:nowrap;font-size:10px;line-height:12px}
  .field{position:absolute;background:var(--field);height:12px}
  .box{display:inline-block;width:7px;height:7px;border:1px solid var(--box);margin-left:1px;vertical-align:-0.5px;background:#fff}
  .bold{font-weight:700}

  /* header */
  .brand{position:absolute;right:26px;top:34px;font-size:23px;line-height:28px;color:#333;letter-spacing:.3px}
  .practice-address{position:absolute;right:26px;top:78px;text-align:right;font-size:8.5px;line-height:11px}
  .form-title{position:absolute;left:25px;top:116px;font-size:11px;letter-spacing:.2px}
  .form-title__rule{position:absolute;left:25px;top:131px;width:512px;height:2px;background:var(--bar)}

  .sub-label{font-size:9.5px}
  .right{text-align:right}

  .section-bar{position:absolute;left:25px;width:512px;height:15px;background:var(--bar);color:#fff;font-size:10px;line-height:15px;padding-left:7px}

  .question{font-size:10.5px}
  .turn-over{position:absolute;right:26px;top:748px;font-size:9.5px}

  /* back page */
  .checklist-title{position:absolute;left:29px;top:36px;height:14px;padding:0 5px;background:var(--bar);color:#fff;font-size:9.5px;font-weight:700;line-height:14px}
  .checklist{position:absolute;top:63px;width:250px;font-size:9px;line-height:11.3px}
  .checklist--a{left:35px}
  .checklist--b{left:299px}
  .group + .group{margin-top:11.3px}
  .group__title{font-weight:700}
  .item{position:relative;height:11.3px;white-space:nowrap}
  .item--small{font-size:7.6px}
  .item .yes,.item .no{position:absolute;top:0;font-size:9px}
  .checklist--a .yes{left:170px}
  .checklist--a .no{left:207px}
  .checklist--b .yes{left:175px}
  .checklist--b .no{left:212px}
  .other-field{height:11px;background:var(--field);margin-top:2px;width:235px}

  .sign-label{position:absolute;top:603px;font-size:8.5px}
  .sign-line{position:absolute;top:610px;height:1px;background:#666}
  .closing-note{position:absolute;left:0;right:0;top:705px;text-align:center;font-size:7.4px;line-height:9px;font-style:italic;color:var(--muted)}
</style>
</head>
<body>

<!-- Page 1: patient information -->
<section class="page page--front">
  <div class="page__frame"></div>

  <div class="brand">harbour dental</div>
  <div class="practice-address">2.04/118 Coastline Rd<br>Kincumber NSW 2251<br>(02) 40 123 456</div>

  <h1 class="form-title">CONFIDENTIAL MEDICAL HISTORY</h1>
  <div class="form-title__rule"></div>

  <!-- patient details -->
  <span class="abs" style="left:25px;top:143px">Name:</span>
  <div class="field" style="left:60px;top:143px;width:70px"></div>
  <div class="field" style="left:132px;top:143px;width:68px"></div>
  <div class="field" style="left:202px;top:143px;width:69px"></div>
  <span class="abs sub-label" style="left:25px;top:156px">Title</span>
  <span class="abs sub-label" style="left:88px;top:156px">First</span>
  <span class="abs sub-label" style="left:157px;top:156px">Middle</span>
  <span class="abs sub-label" style="left:229px;top:156px">Last</span>

  <span class="abs" style="left:25px;top:175px">Address:</span>
  <div class="field" style="left:70px;top:175px;width:201px"></div>
  <span class="abs" style="left:25px;top:192px">DOB:</span>
  <div class="field" style="left:51px;top:192px;width:220px"></div>
  <span class="abs" style="left:25px;top:210px">Email Address:</span>
  <div class="field" style="left:91px;top:210px;width:180px"></div>
  <span class="abs" style="left:25px;top:228px">Phone Number(s):</span>
  <span class="abs right" style="right:451px;top:245px">Mobile:</span>
  <div class="field" style="left:113px;top:245px;width:158px"></div>
  <span class="abs right" style="right:451px;top:263px">Work:</span>
  <div class="field" style="left:113px;top:263px;width:158px"></div>
  <span class="abs right" style="right:451px;top:280px">Home:</span>
  <div class="field" style="left:113px;top:280px;width:158px"></div>

  <!-- general practitioner -->
  <span class="abs bold" style="left:289px;top:143px">GENERAL PRACTITIONER:</span>
  <span class="abs" style="left:289px;top:158px">Name:</span>
  <div class="field" style="left:320px;top:158px;width:217px"></div>
  <span class="abs" style="left:289px;top:172px">Practice Name:</span>
  <div class="field" style="left:362px;top:172px;width:175px"></div>
  <span class="abs" style="left:289px;top:186px">Phone Number:</span>
  <div class="field" style="left:363px;top:186px;width:174px"></div>
  <span class="abs" style="left:289px;top:200px">Do you have a health fund with dental cover? <b>Yes</b> or <b>No</b></span>
  <span class="abs" style="left:289px;top:212px">If so, what is the name of the fund?</span>
  <div class="field" style="left:289px;top:225px;width:248px"></div>
  <span class="abs" style="left:289px;top:237px">Fund Number?</span>
  <div class="field" style="left:355px;top:237px;width:182px"></div>
  <span class="abs" style="left:289px;top:251px">Priority Number on card: &nbsp;&nbsp;&nbsp;<b>0&nbsp;&nbsp;1&nbsp;&nbsp;2&nbsp;&nbsp;3&nbsp;&nbsp;4&nbsp;&nbsp;5</b></span>
  <span class="abs" style="left:289px;top:265px">Occupation:</span>
  <div class="field" style="left:349px;top:265px;width:188px"></div>
  <span class="abs" style="left:289px;top:280px">Referred by:</span>
  <div class="field" style="left:349px;top:280px;width:188px"></div>

  <!-- allergies -->
  <div class="section-bar" style="top:322px">Please indicate if &nbsp;you are allergic to any of the following <span class="box" style="border-color:#fff;background:transparent"></span> ?</div>
  <span class="abs" style="left:31px;top:342px">Aspirin<span class="box"></span></span>
  <span class="abs" style="left:83px;top:342px">Codeine<span class="box"></span></span>
  <span class="abs" style="left:145px;top:342px">Penicillin<span class="box"></span></span>
  <span class="abs" style="left:206px;top:342px">Sulfites<span class="box"></span></span>
  <span class="abs" style="left:260px;top:342px">Latex<span class="box"></span></span>
  <span class="abs" style="left:307px;top:342px">Local<span class="box"></span></span>
  <span class="abs" style="left:356px;top:342px">Anaesthetic<span class="box"></span></span>
  <span class="abs" style="left:432px;top:342px">Lactose<span class="box"></span></span>
  <span class="abs" style="left:491px;top:342px">Nickel<span class="box"></span></span>
  <span class="abs" style="left:31px;top:361px">Other</span>
  <div class="field" style="left:57px;top:361px;width:480px"></div>

  <!-- medications -->
  <div class="section-bar" style="top:401px">Are you currently taking, or have ever taken, any of the following medication <span class="box" style="border-color:#fff;background:transparent"></span> ?</div>
  <span class="abs" style="left:31px;top:420px">Asthma inhaler <span class="box"></span></span>
  <span class="abs" style="left:136px;top:420px">Anti-epileptics <span class="box"></span></span>
  <span class="abs" style="left:236px;top:420px">Anti-depressants<span class="box"></span></span>
  <span class="abs" style="left:345px;top:420px">Blood Pressure <span class="box"></span></span>
  <span class="abs" style="left:446px;top:420px">Blood Thinners <span class="box"></span></span>
  <span class="abs" style="left:31px;top:439px">Bisphosphonates<span class="box"></span></span>
  <span class="abs" style="left:136px;top:439px">Chemotherapy<span class="box"></span></span>
  <span class="abs" style="left:236px;top:439px">Insulin<span class="box"></span></span>
  <span class="abs" style="left:331px;top:439px">Immunosuppressants<span class="box"></span></span>
  <span class="abs" style="left:446px;top:439px">Steroids<span class="box"></span></span>
  <span class="abs" style="left:31px;top:458px">Oral Contraceptive<span class="box"></span></span>
  <span class="abs" style="left:135px;top:458px">Other<span class="box"></span></span>

  <div class="section-bar" style="top:487px">Please specify medication name, dose, and frequency where possible:</div>
  <div class="field" style="left:32px;top:510px;width:164px;height:11px"></div>
  <div class="field" style="left:200px;top:510px;width:164px;height:11px"></div>
  <div class="field" style="left:368px;top:510px;width:164px;height:11px"></div>
  <div class="field" style="left:32px;top:531px;width:164px;height:11px"></div>
  <div class="field" style="left:200px;top:531px;width:164px;height:11px"></div>
  <div class="field" style="left:368px;top:531px;width:164px;height:11px"></div>
  <div class="field" style="left:32px;top:549px;width:164px;height:11px"></div>
  <div class="field" style="left:200px;top:549px;width:164px;height:11px"></div>
  <div class="field" style="left:368px;top:549px;width:164px;height:11px"></div>

  <span class="abs question" style="left:25px;top:581px"><b>Do you require antibiotic cover?</b>&nbsp; Yes<span class="box"></span>&nbsp; No<span class="box"></span></span>
  <span class="abs question" style="left:25px;top:610px"><b>Have you had a joint replacement?</b>&nbsp; Yes<span class="box"></span>&nbsp; No<span class="box"></span></span>
  <span class="abs question bold" style="left:25px;top:639px">Women:</span>
  <span class="abs question" style="left:25px;top:654px"><b>Are you pregnant?</b>&nbsp; Yes<span class="box"></span>&nbsp; No<span class="box"></span> <b>Possible or Breast Feeding?</b>&nbsp; Yes<span class="box"></span>&nbsp; No<span class="box"></span></span>

  <div class="turn-over">PLEASE TURN OVER</div>
</section>

<!-- Page 2: medical history checklist -->
<section class="page page--back">
  <div class="page__frame"></div>

  <div class="checklist-title">Do you have, or have you had, any of the following?</div>

  <div class="checklist checklist--a">
    <div class="group">
      <div class="group__title">Dental</div>
      <div class="item">Acid Reflux<span class="yes">Yes<span class="box"></span></span><span class="no">No<span class="box"></span></span></div>
      <div class="item">Bad Breath/Taste<span class="yes">Yes<span class="box"></span></span><span class="no">No<span class="box"></span></span></div>
      <div class="item">Bleeding/Swollen/Sore Gums<span class="yes">Yes<span class="box"></span></span><span class="no">No<span class="box"></span></span></div>
      <div class="item">Blisters/Ulcers in Mouth<span class="yes">Yes<span class="box"></span></span><span class="no">No<span class="box"></span></span></div>
      <div class="item">Broken tooth/filling<span class="yes">Yes<span class="box"></span></span><span class="no">No<span class="box"></span></span></div>
      <div class="item">Burning tongue<span class="yes">Yes<span class="box"></span></span><span class="no">No<span class="box"></span></span></div>
      <div class="item">Dry mouth<span class="yes">Yes<span class="box"></span></span><span class="no">No<span class="box"></span></span></div>
      <div class="item">Food collection between teeth<span class="yes">Yes<span class="box"></span></span><span class="no">No<span class="box"></span></span></div>
      <div class="item">Grinding/clenching teeth (day/night)<span class="yes">Yes<span class="box"></span></span><span class="no">No<span class="box"></span></span></div>
      <div class="item">Loose teeth<span class="yes">Yes<span class="box"></span></span><span class="no">No<span class="box"></span></span></div>
      <div class="item">Crooked teeth<span class="yes">Yes<span class="box"></span></span><span class="no">No<span class="box"></span></span></div>
      <div class="item">Discoloured teeth<span class="yes">Yes<span class="box"></span></span><span class="no">No<span class="box"></span></span></div>
      <div class="item">Sensitivity to Hot/Cold<span class="yes">Yes<span class="box"></span></span><span class="no">No<span class="box"></span></span></div>
      <div class="item">Tooth pain when chewing<span class="yes">Yes<span class="box"></span></span><span class="no">No<span class="box"></span></span></div>
      <div class="item">Jaw pain/Fracture<span class="yes">Yes<span class="box"></span></span><span class="no">No<span class="box"></span></span></div>
      <div class="item">Orthodontic treatment/history<span class="yes">Yes<span class="box"></span></span><span class="no">No<span class="box"></span></span></div>
      <div class="item">Oral Cancer<span class="yes">Yes<span class="box"></span></span><span class="no">No<span class="box"></span></span></div>
    </div>
    <div class="group">
      <div class="group__title">Diet/Lifestyle</div>
      <div class="item item--small">Drink more than one glass alcohol per day<span class="yes">Yes<span class="box"></span></span><span class="no">No<span class="box"></span></span></div>
      <div class="item">Smoking<span class="yes">Yes<span class="box"></span></span><span class="no">No<span class="box"></span></span></div>
      <div class="item">Carbonated drinks<span class="yes">Yes<span class="box"></span></span><span class="no">No<span class="box"></span></span></div>
      <div class="item">Sugary foods</div>
    </div>
    <div class="group">
      <div class="group__title">Blood</div>
      <div class="item">Anaemia<span class="yes">Yes<span class="box"></span></span><span class="no">No<span class="box"></span></span></div>
      <div class="item">Blood clots<span class="yes">Yes<span class="box"></span></span><span class="no">No<span class="box"></span></span></div>
      <div class="item">Leukemia<span class="yes">Yes<span class="box"></span></span><span class="no">No<span class="box"></span></span></div>
      <div class="item">Low platelets<span class="yes">Yes<span class="box"></span></span><span class="no">No<span class="box"></span></span></div>
      <div class="item">Lymphoma<span class="yes">Yes<span class="box"></span></span><span class="no">No<span class="box"></span></span></div>
      <div class="item">Haemophelia<span class="yes">Yes<span class="box"></span></span><span class="no">No<span class="box"></span></span></div>
    </div>
    <div class="group">
      <div class="group__title">Chest</div>
      <div class="item">Bronchitis<span class="yes">Yes<span class="box"></span></span><span class="no">No<span class="box"></span></span></div>
      <div class="item">Cystic Fibrosis<span class="yes">Yes<span class="box"></span></span><span class="no">No<span class="box"></span></span></div>
      <div class="item">Emphysema<span class="yes">Yes<span class="box"></span></span><span class="no">No<span class="box"></span></span></div>
      <div class="item">Pneumonia<span class="yes">Yes<span class="box"></span></span><span class="no">No<span class="box"></span></span></div>
    </div>
    <div class="group">
      <div class="group__title">Infectious Disease</div>
      <div class="item">Creutzfeldt-Jakob Disease<span class="yes">Yes<span class="box"></span></span><span class="no">No<span class="box"></span></span></div>
      <div class="item">Hepatitis A,B,C,D<span class="yes">Yes<span class="box"></span></span><span class="no">No<span class="box"></span></span></div>
      <div class="item">HIV/AIDS<span class="yes">Yes<span class="box"></span></span><span class="no">No<span class="box"></span></span></div>
    </div>
  </div>

  <div class="checklist checklist--b">
    <div class="group">
      <div class="item">Influenza<span class="yes">Yes<span class="box"></span></span><span class="no">No<span class="box"></span></span></div>
      <div class="item">Shingles<span class="yes">Yes<span class="box"></span></span><span class="no">No<span class="box"></span></span></div>
      <div class="item">Tuberculosis<span class="yes">Yes<span class="box"></span></span><span class="no">No<span class="box"></span></span></div>
    </div>
    <div class="group" style="margin-top:14px">
      <div class="group__title">Heart</div>
      <div class="item">Angina<span class="yes">Yes<span class="box"></span></span><span class="no">No<span class="box"></span></span></div>
      <div class="item">Atrial Fibrillation<span class="yes">Yes<span class="box"></span></span><span class="no">No<span class="box"></span></span></div>
      <div class="item">Blood Pressure (High/Low)<span class="yes">Yes<span class="box"></span></span><span class="no">No<span class="box"></span></span></div>
      <div class="item">Congenital Heart Disease<span class="yes">Yes<span class="box"></span></span><span class="no">No<span class="box"></span></span></div>
      <div class="item">Heart attack<span class="yes">Yes<span class="box"></span></span><span class="no">No<span class="box"></span></span></div>
      <div class="item">Heart murmur<span class="yes">Yes<span class="box"></span></span><span class="no">No<span class="box"></span></span></div>
      <div class="item">Heart surgery<span class="yes">Yes<span class="box"></span></span><span class="no">No<span class="box"></span></span></div>
      <div class="item">Heart valve replacement<span class="yes">Yes<span class="box"></span></span><span class="no">No<span class="box"></span></span></div>
      <div class="item">Infective endocarditis<span class="yes">Yes<span class="box"></span></span><span class="no">No<span class="box"></span></span></div>
      <div class="item">Rheumatic Heart Disease<span class="yes">Yes<span class="box"></span></span><span class="no">No<span class="box"></span></span></div>
      <div class="item">Pacemaker<span class="yes">Yes<span class="box"></span></span><span class="no">No<span class="box"></span></span></div>
      <div class="item">Stent<span class="yes">Yes<span class="box"></span></span><span class="no">No<span class="box"></span></span></div>
    </div>
    <div class="group" style="margin-top:14px">
      <div class="group__title">Other</div>
      <div class="item">Anxiety/PTSD<span class="yes">Yes<span class="box"></span></span><span class="no">No<span class="box"></span></span></div>
      <div class="item">Arthritis<span class="yes">Yes<span class="box"></span></span><span class="no">No<span class="box"></span></span></div>
      <div class="item">Alzheimer's<span class="yes">Yes<span class="box"></span></span><span class="no">No<span class="box"></span></span></div>
      <div class="item">Asthma<span class="yes">Yes<span class="box"></span></span><span class="no">No<span class="box"></span></span></div>
      <div class="item">Anaphylaxis<span class="yes">Yes<span class="box"></span></span><span class="no">No<span class="box"></span></span></div>
      <div class="item">Auto-immune disease<span class="yes">Yes<span class="box"></span></span><span class="no">No<span class="box"></span></span></div>
      <div class="item">Coeliac<span class="yes">Yes<span class="box"></span></span><span class="no">No<span class="box"></span></span></div>
      <div class="item">Depression<span class="yes">Yes<span class="box"></span></span><span class="no">No<span class="box"></span></span></div>
      <div class="item">Diabetes<span class="yes">Yes<span class="box"></span></span><span class="no">No<span class="box"></span></span></div>
      <div class="item">Epilepsy<span class="yes">Yes<span class="box"></span></span><span class="no">No<span class="box"></span></span></div>
      <div class="item">Kidney Disease<span class="yes">Yes<span class="box"></span></span><span class="no">No<span class="box"></span></span></div>
      <div class="item">Liver Disease<span class="yes">Yes<span class="box"></span></span><span class="no">No<span class="box"></span></span></div>
      <div class="item">Osteoporosis<span class="yes">Yes<span class="box"></span></span><span class="no">No<span class="box"></span></span></div>
      <div class="item">Parkinson's<span class="yes">Yes<span class="box"></span></span><span class="no">No<span class="box"></span></span></div>
      <div class="item">Radiation to Head/Neck<span class="yes">Yes<span class="box"></span></span><span class="no">No<span class="box"></span></span></div>
      <div class="item">Schizophrenia<span class="yes">Yes<span class="box"></span></span><span class="no">No<span class="box"></span></span></div>
      <div class="item">Snoring<span class="yes">Yes<span class="box"></span></span><span class="no">No<span class="box"></span></span></div>
      <div class="item">Sleep apnea<span class="yes">Yes<span class="box"></span></span><span class="no">No<span class="box"></span></span></div>
      <div class="item">Stroke<span class="yes">Yes<span class="box"></span></span><span class="no">No<span class="box"></span></span></div>
    </div>
    <div class="group" style="margin-top:9px">
      <div class="group__title">Other</div>
      <div class="other-field"></div>
      <div class="other-field"></div>
    </div>
  </div>

  <span class="sign-label" style="left:35px">SIGNATURE</span>
  <div class="sign-line" style="left:85px;width:178px"></div>
  <span class="sign-label" style="left:331px">DATE</span>
  <div class="sign-line" style="left:356px;width:178px"></div>

  <p class="closing-note">Thank you for the time to complete your medical history form.<br>Oral health is linked to overall health and this comprehensive questionnaire will help us to provide you with optimal and safe care.</p>
</section>

</body>
</html>
```